Harborline Benches business cards

I’d like a business card design that includes my logo, a tag line and my contact info. Black, textured background. My contact info color should match the orange and blue gradients. Tagline under logo: “Wooden Tables and Furniture of the Highest Quality”

Target Market(s)

High end furniture buyers

Contact Information for Business Card

Contact info, logo and tagline

```html
<!DOCTYPE html>
<html lang="en">
<head>
<meta charset="utf-8">
<title>Harborline Benches Business Cards</title>
<link rel="stylesheet" href="https://fonts.googleapis.com/css2?family=Open+Sans:wght@600&family=Poppins:wght@400;500&display=swap">
<style>
  :root {
    --page-bg: #3b3b3d;
    --card-front: #ffffff;
    --card-back-dark: #1c1f25;
    --card-back-mid: #2e333c;
    --orange: #ee7623;
    --orange-soft: #f6b27f;
    --blue: #1a56b0;
    --ink: #1e1e1e;
    --ink-soft: #333333;
    --white: #ffffff;
  }
  * { margin: 0; padding: 0; box-sizing: border-box; }
  html, body {
    width: 1093px; height: 1200px; overflow: hidden;
    background: var(--page-bg);
  }
  .sheet { position: relative; width: 1093px; height: 1200px; }

  .card {
    position: absolute;
    left: 265px;
    border-radius: 24px;
    overflow: hidden;
  }

  /* Front */
  .card-front {
    top: 226px; width: 577px; height: 356px;
    background: var(--card-front);
  }
  .tree-art {
    position: absolute; top: 0; right: 0;
    width: 303px; height: 100%;
    background: linear-gradient(180deg, var(--orange-soft) 0%, var(--orange) 100%);
    opacity: 0.85;
  }
  .identity { position: absolute; left: 34px; top: 118px; }
  .person-name {
    font-family: "Open Sans", sans-serif; font-weight: 600;
    font-size: 30px; line-height: 1; letter-spacing: -0.2px;
  }
  .person-name .first { color: var(--orange); }
  .person-name .last { color: var(--blue); }
  .person-role {
    font-family: "Poppins", sans-serif; font-size: 17px;
    color: var(--ink-soft); margin-top: 1px;
  }
  .contact-list {
    position: absolute; left: 35px; top: 181px;
    list-style: none;
    font-family: "Poppins", sans-serif; font-size: 17.5px; color: var(--ink);
  }
  .contact-list li {
    display: flex; align-items: center; gap: 7px; height: 21px;
  }
  .contact-list svg { width: 15px; height: 15px; flex: none; }
  .contact-list .accent { color: var(--orange); }
  .address {
    position: absolute; left: 36px; top: 257px;
    font-family: "Poppins", sans-serif; font-size: 17.5px;
    line-height: 21px; color: var(--ink); font-style: normal;
  }

  /* Back */
  .card-back {
    top: 621px; width: 582px; height: 356px;
    background: linear-gradient(165deg, var(--card-back-dark) 0%, var(--card-back-mid) 45%, var(--card-back-dark) 75%, var(--card-back-mid) 100%);
  }
  .brand-block {
    position: absolute; left: 0; right: 0; top: 170px;
    text-align: center;
  }
  .brand-name {
    font-family: "Poppins", sans-serif; font-weight: 500;
    font-size: 38px; line-height: 1; color: var(--orange);
  }
  .tagline {
    margin-top: 36px;
    font-family: "Poppins", sans-serif; font-size: 17.5px;
    color: var(--white);
  }
</style>
</head>
<body>
<main class="sheet">
  <section class="card card-front">
    <div class="tree-art" role="img" aria-label="Orange bare tree illustration with spreading branches"></div>
    <div class="identity">
      <h1 class="person-name"><span class="first">Daniel</span> <span class="last">Reeves</span></h1>
      <p class="person-role">Managing Director</p>
    </div>
    <ul class="contact-list">
      <li>
        <svg viewBox="0 0 16 16" aria-hidden="true"><path d="M3 1.5 5.5 1l1.5 3.5-1.8 1.2a8 8 0 0 0 5 5L11.5 9 15 10.5 14.5 13c-.3 1.2-1.5 1.8-2.7 1.5C6.7 13.2 2.8 9.3 1.5 4.2 1.2 3 1.8 1.8 3 1.5Z" fill="var(--orange)"/></svg>
        044-318 270 645
      </li>
      <li>
        <svg viewBox="0 0 16 16" aria-hidden="true"><rect x="0.5" y="3" width="15" height="10" fill="var(--orange)"/><path d="M0.5 3 8 9l7.5-6" fill="none" stroke="#fff" stroke-width="1.2"/></svg>
        info@harborline.co
      </li>
      <li>
        <svg viewBox="0 0 16 16" aria-hidden="true"><g fill="none" stroke="var(--orange)" stroke-width="1.3"><circle cx="8" cy="8" r="6.8"/><ellipse cx="8" cy="8" rx="3" ry="6.8"/><path d="M1.2 8h13.6M2.5 4.5h11M2.5 11.5h11"/></g></svg>
        <span>www.<span class="accent">harborline</span>.co</span>
      </li>
    </ul>
    <address class="address">58, Wharf Street, Suite 12<br>30217,Eastmere Bay</address>
  </section>

  <section class="card card-back">
    <div class="brand-block">
      <p class="brand-name">Harborline Benches</p>
      <p class="tagline">Wooden Tables and Furniture of the Highest Quality</p>
    </div>
  </section>
</main>
</body>
</html>
```